Website for Torvel Capital - investment banking firm

We have a corporate identity (thanks to Ravinka/31842) and want to extend that into a website design.  See the attached zipped files.
We have software folks in-house to do the coding.
See the attached Project Brief & Notes for more details.  Don't worry about the actual text - lorem ipsum will be fine.
The server will be Apache.
Thank you!
Desmond

Industry/Entity Type
Investment

```html
<!DOCTYPE html>
<html lang="en">
<head>
<meta charset="utf-8">
<title>Torvel Capital</title>
<link href="https://fonts.googleapis.com/css2?family=Open+Sans:wght@400;600;700&display=swap" rel="stylesheet">
<style>
:root{
  --blue:#1d5fab;
  --blue-dark:#164c8c;
  --navy:#143e70;
  --ink:#333;
  --muted:#8a8a8a;
  --line:#e3e3e3;
  --footer:#2b2b2b;
  --footer-deep:#1b1b1b;
  --white:#fff;
}
*{box-sizing:border-box;margin:0;padding:0}
html,body{width:764px;height:1200px;overflow:hidden}
body{font-family:"Open Sans",Arial,sans-serif;color:var(--ink);background:var(--white);font-size:9px;line-height:1.45}
.page{position:relative;width:764px;height:1200px}

/* header */
.masthead{height:74px;display:flex;align-items:center;justify-content:space-between;padding:0 118px 0 112px}
.brand{display:flex;align-items:center;gap:7px;font-size:19px;font-weight:700;color:var(--navy)}
.brand-mark{width:22px;height:22px;border-radius:50%;background:var(--navy)}
.account{font-size:9px;color:var(--blue);display:flex;gap:8px}
.account span.sep{color:var(--muted)}

.main-nav{height:24px;background:var(--blue);display:flex;align-items:center;padding-left:118px;gap:26px}
.main-nav a{color:var(--white);font-size:8.5px;text-decoration:none}

/* hero */
.hero{position:relative;height:322px;background:radial-gradient(ellipse at 60% 50%,#6d7a86 0%,#3f4a55 55%,#1f262d 100%)}
.hero-caption{position:absolute;left:118px;top:138px;width:420px;padding:10px 16px;background:rgba(20,40,70,.55);color:var(--white);font-size:16px;line-height:1.35}
.hero-arrow{position:absolute;top:150px;width:22px;height:22px;border-radius:50%;background:rgba(0,0,0,.45)}
.hero-arrow.prev{left:86px}.hero-arrow.next{right:86px}
.hero-arrow svg{display:block}
.hero-dots{position:absolute;bottom:10px;left:50%;transform:translateX(-50%);display:flex;gap:5px}
.hero-dots i{width:6px;height:6px;border-radius:50%;background:rgba(255,255,255,.5)}
.hero-dots i.on{background:var(--white)}

/* welcome */
.welcome{height:82px;background:var(--blue);color:var(--white);padding:12px 118px;position:relative}
.welcome h1{font-size:13px;font-weight:600;margin-bottom:3px}
.welcome p{width:470px;font-size:7.5px;opacity:.9}
.btn{display:inline-block;background:var(--white);color:var(--blue);font-size:7.5px;padding:5px 14px;border-radius:2px}
.welcome .btn{position:absolute;right:118px;top:32px}

/* services */
.services{display:flex;justify-content:center;gap:20px;padding:24px 0 14px}
.service{width:118px;text-align:center}
.service-icon{width:58px;height:58px;margin:0 auto 8px;border-radius:50%;border:3px solid var(--line);display:flex;align-items:center;justify-content:center}
.service h3{font-size:8.5px;font-weight:600;margin-bottom:4px}
.service p{font-size:6.5px;color:var(--muted)}

/* feature columns */
.features{display:flex;justify-content:center;gap:22px;padding:8px 0 0}
.feature{width:160px}
.feature h2{font-size:11px;color:var(--blue);font-weight:600;margin-bottom:6px}
.feature-photo{height:82px;margin-bottom:7px}
.feature p{font-size:6.5px;color:#555;margin-bottom:8px}
.btn-blue{display:inline-block;background:var(--blue);color:var(--white);font-size:7px;padding:4px 11px;border-radius:2px}

/* clients */
.clients{padding:22px 118px 0}
.clients h2{font-size:11px;color:var(--blue);font-weight:600;margin-bottom:12px}
.client-row{display:flex;justify-content:space-between;align-items:center;height:30px}
.client{display:flex;align-items:center;gap:5px;font-size:10px;font-weight:600;color:#9a9a9a}
.client i{width:12px;height:12px;border-radius:50%;background:#bdbdbd}

/* footer */
.site-footer{position:absolute;left:0;top:1018px;width:764px;height:158px;background:var(--footer);color:#ccc;display:flex;gap:24px;padding:14px 118px}
.site-footer h4{font-size:8px;color:var(--white);font-weight:600;margin-bottom:7px}
.locations{width:170px}
.map{height:100px;background:linear-gradient(135deg,#d9e1c9,#c8d6e4)}
.news{width:170px}
.news-item{display:flex;gap:6px;margin-bottom:9px}
.news-thumb{width:34px;height:28px;flex:none;background:linear-gradient(135deg,#6b7a8a,#3c4855)}
.news-item p{font-size:6.5px}
.news-item .date{color:var(--blue);font-size:6px}
.contact{flex:1}
.contact li{list-style:none;display:flex;gap:6px;align-items:flex-start;font-size:6.5px;margin-bottom:6px}
.contact svg{flex:none;margin-top:1px}

.legal{position:absolute;left:0;top:1176px;width:764px;height:24px;background:var(--footer-deep);color:#999;font-size:6.5px;display:flex;justify-content:space-between;align-items:center;padding:0 118px}
</style>
</head>
<body>
<div class="page">

  <header class="masthead">
    <div class="brand"><span class="brand-mark"></span>Torvel Capital</div>
    <nav class="account"><span>Login</span><span class="sep">|</span><span>Register</span></nav>
  </header>

  <nav class="main-nav">
    <a>Home</a><a>About</a><a>Services</a><a>Current Engagements</a><a>Completed Transactions</a><a>Contact</a>
  </nav>

  <section class="hero" role="img" aria-label="Photograph of dartboard targets with a blue target in focus">
    <div class="hero-caption">We assist corporate clients and private equity groups to identify opportunities for growth by acquisition</div>
    <span class="hero-arrow prev"><svg width="22" height="22"><path d="M13 6 8 11l5 5" fill="none" stroke="#fff" stroke-width="2"/></svg></span>
    <span class="hero-arrow next"><svg width="22" height="22"><path d="M9 6l5 5-5 5" fill="none" stroke="#fff" stroke-width="2"/></svg></span>
    <div class="hero-dots"><i class="on"></i><i></i><i></i></div>
  </section>

  <section class="welcome">
    <h1>Welcome To Torvel Capital</h1>
    <p>Torvel Capital is an independent investment bank working for buyers in a number of industries. We utilize exceptional technology in finding companies to meet our clients' search criteria, and we report progress to each client at every step of our work.</p>
    <span class="btn">Read More</span>
  </section>

  <section class="services">
    <div class="service">
      <div class="service-icon"><svg width="26" height="26"><path d="M3 22h20M6 20v-6M11 20V9M16 20v-8M21 20V5" stroke="#1d5fab" stroke-width="3"/></svg></div>
      <h3>Strategic Advisory</h3>
      <p>We assist corporate clients and private equity groups to identify opportunities for growth by acquisition.</p>
    </div>
    <div class="service">
      <div class="service-icon"><svg width="26" height="26"><circle cx="13" cy="13" r="10" fill="none" stroke="#1d5fab" stroke-width="3"/><path d="M13 7v6l4 3" fill="none" stroke="#1d5fab" stroke-width="2.5"/></svg></div>
      <h3>Current Engagements</h3>
      <p>We assist corporate clients and private equity groups to identify opportunities for growth by acquisition.</p>
    </div>
    <div class="service">
      <div class="service-icon"><svg width="26" height="26"><path d="M5 13l6 6L22 7" fill="none" stroke="#1d5fab" stroke-width="3.5"/></svg></div>
      <h3>Completed Transactions</h3>
      <p>We assist corporate clients and private equity groups to identify opportunities for growth by acquisition.</p>
    </div>
    <div class="service">
      <div class="service-icon"><svg width="26" height="26"><path d="M13 3 4 7v6c0 5 4 9 9 10 5-1 9-5 9-10V7z" fill="#1d5fab"/></svg></div>
      <h3>Regulatory Compliance</h3>
      <p>We assist corporate clients and private equity groups to identify opportunities for growth by acquisition.</p>
    </div>
  </section>

  <section class="features">
    <article class="feature">
      <h2>Who We Are</h2>
      <div class="feature-photo" role="img" aria-label="Photograph of a city skyline of office towers" style="background:linear-gradient(180deg,#9fbbd6,#5b7a97)"></div>
      <p>Torvel Capital has a diverse array of clients ranging from multi-billion dollar strategic acquirers to large private equity firms. We work closely with each buyer to understand exactly what they are looking for and deliver results.</p>
      <span class="btn-blue">Read More</span>
    </article>
    <article class="feature">
      <h2>Our Process</h2>
      <div class="feature-photo" role="img" aria-label="Photograph of a hand drawing a business process diagram" style="background:linear-gradient(180deg,#e9ecef,#b9c3cc)"></div>
      <p>Once we have your acquisition parameters, we feed those into our software to create an initial target list. Our research team reviews the list and refines it by geography, revenue, ownership and sector fit.</p>
      <span class="btn-blue">Read More</span>
    </article>
    <article class="feature">
      <h2>Our Team</h2>
      <div class="feature-photo" role="img" aria-label="Photograph of a business team standing together in an office" style="background:linear-gradient(180deg,#d4d8dc,#7f8b96)"></div>
      <p>Torvel Capital's team of bankers and advisors is comprised of experienced professionals. Our research team is critical in finding deals where there is sufficient strategic overlap to create value.</p>
      <span class="btn-blue">Read More</span>
    </article>
  </section>

  <section class="clients">
    <h2>Our Clients</h2>
    <div class="client-row">
      <span class="client"><i></i>Ardent</span>
      <span class="client"><i></i>Your Logo</span>
      <span class="client"><i></i>Business</span>
      <span class="client"><i></i>Brand</span>
      <span class="client"><i></i>Designer</span>
      <span class="client"><i></i>Logo</span>
    </div>
  </section>

  <footer class="site-footer">
    <div class="locations">
      <h4>Global Investment Banking Service Locations</h4>
      <div class="map" role="img" aria-label="Map showing the office location"></div>
    </div>
    <div class="news">
      <h4>Latest News</h4>
      <div class="news-item">
        <div class="news-thumb" role="img" aria-label="News photograph"></div>
        <p>New regional desk opens with two senior partners<br><span class="date">May 2, 2014</span></p>
      </div>
      <div class="news-item">
        <div class="news-thumb" role="img" aria-label="News photograph"></div>
        <p>Quarterly review highlights strong deal activity<br><span class="date">April 18, 2014</span></p>
      </div>
    </div>
    <div class="contact">
      <h4>Contact</h4>
      <ul>
        <li><svg width="8" height="8"><circle cx="4" cy="2.5" r="2" fill="#1d5fab"/><path d="M0 8c0-3 8-3 8 0z" fill="#1d5fab"/></svg>Desmond Arlow</li>
        <li><svg width="8" height="8"><path d="M1 1h2l1 2-1 1c1 1 1 1 2 2l1-1 2 1v2C4 8 0 4 1 1z" fill="#1d5fab"/></svg>+852 3100 4470</li>
        <li><svg width="8" height="8"><rect x="0" y="1" width="8" height="6" fill="#1d5fab"/><path d="M0 1l4 3 4-3" fill="none" stroke="#2b2b2b"/></svg>desmond@torvelcapital.com</li>
        <li><svg width="8" height="8"><path d="M4 0a3 3 0 0 1 3 3c0 2-3 5-3 5S1 5 1 3a3 3 0 0 1 3-3z" fill="#1d5fab"/></svg>18/F Harbour Tower, Central,<br>Hong Kong</li>
      </ul>
    </div>
  </footer>

  <div class="legal">
    <span>About | Help | Contact Us | Newsletter Login | Privacy Policy | Terms of Service</span>
    <span>Copyright 2014 Torvel Capital. All Rights Reserved</span>
  </div>

</div>
</body>
</html>
```